The design should look similar to the uploaded example to accommodate the information needed for a business card template. I would like to see the colors orange and charcoal grey incorporated along with the logo.The following should be on the back of the card SPECIALIZING IN NEW AND USED TIRES & WHEELS FOR:- Loaders- Skid Steers- Telehandlers- Boom Lifts- Forklifs and moreELIMINATING DOWNTIMEWheel Exchange Program for New & Used Foam Filled and Solid Rubber TiresSPECIALTY SERVICES- Foam Filling Tires- Largest Tire Press in SE- ONSITE Forklift Tire Press- Boom Truck Services - Rubber Tracks

Target Market(s)

New and Existing Customers

Industry/Entity Type

Business

Contact Information for Business Card

NAMEHEAVY DUTY TIRE, LLC8470 Belvedere RoadWest Palm Beach, FL 33411P: 844-HD-TIRESF: 561-431-6469C:E: W: WWW.GRANITERIMSUPPLY-EXAMPLE.COM

Font styles to use
Sans Serif

Colors
f37122
333333

Requirements
Must have
• The logo and the information indicated for the backside of the card
Nice to have
• Keep the orange and charcoal grey colors

```html
<!DOCTYPE html>
<html lang="en">
<head>
<meta charset="utf-8">
<title>Granite Rim Supply, LLC — Business Card</title>
<link rel="stylesheet" href="https://fonts.googleapis.com/css2?family=Open+Sans:wght@400;600;700;800&display=swap">
<style>
  :root {
    --bg: #e9e6e1;
    --charcoal: #3a4753;
    --charcoal-deep: #2f3a44;
    --ink: #333333;
    --orange: #f37122;
    --white: #ffffff;
    --muted: #c9d0d6;
  }
  * { box-sizing: border-box; margin: 0; padding: 0; }
  html, body { width: 1200px; height: 950px; overflow: hidden; }
  body {
    background: var(--bg);
    font-family: "Open Sans", Arial, sans-serif;
    position: relative;
  }
  .card {
    position: absolute;
    left: 280px;
    width: 640px;
    height: 366px;
    border-radius: 4px;
    overflow: hidden;
    box-shadow: 0 10px 28px rgba(0,0,0,.22);
  }

  /* Back */
  .card-back {
    top: 70px;
    background: var(--charcoal);
    color: var(--white);
    text-align: center;
    padding-top: 26px;
  }
  .back-mark {
    display: inline-flex;
    align-items: center;
    gap: 12px;
    margin-bottom: 22px;
  }
  .mark-dot {
    width: 40px; height: 40px; border-radius: 50%;
    background: var(--orange);
  }
  .back-mark .mark-name {
    font-weight: 800; font-size: 20px; letter-spacing: .5px; color: var(--white);
  }
  .service-heading {
    font-weight: 700; font-size: 15px; letter-spacing: .4px; text-transform: uppercase;
    margin-top: 12px;
  }
  .service-line {
    font-size: 14px; color: var(--muted); margin-top: 3px;
  }
  .service-line .dot { color: var(--orange); padding: 0 6px; }

  /* Front */
  .card-front {
    top: 514px;
    background: var(--white);
  }
  .front-brand {
    height: 156px;
    display: flex;
    align-items: center;
    justify-content: center;
    gap: 20px;
  }
  .front-brand .mark-dot { width: 74px; height: 74px; }
  .front-brand .mark-name {
    font-weight: 800; font-size: 34px; color: var(--ink); letter-spacing: .5px; line-height: 1.05;
  }
  .front-band {
    position: absolute;
    left: 0; right: 0; bottom: 0; top: 162px;
    background: var(--charcoal);
    border-top: 3px solid var(--orange);
    display: flex;
    align-items: center;
    justify-content: center;
  }
  .front-band::before {
    content: ""; position: absolute; left: 0; right: 0; top: -9px; height: 3px; background: var(--orange); opacity: 0;
  }
  .person {
    text-align: right;
    padding-right: 26px;
    color: var(--white);
    font-size: 16px;
    line-height: 1.45;
  }
  .person-name { color: var(--orange); font-weight: 600; font-size: 20px; }
  .divider { width: 1px; height: 128px; background: rgba(255,255,255,.55); }
  .contacts {
    list-style: none;
    padding-left: 26px;
    color: var(--white);
    font-size: 16px;
    line-height: 1.55;
  }
  .contacts li { display: flex; align-items: center; gap: 12px; }
  .contacts svg { width: 16px; height: 16px; fill: var(--orange); flex: none; }
</style>
</head>
<body>

<section class="card card-back" aria-label="Card back">
  <div class="back-mark">
    <span class="mark-dot"></span>
    <span class="mark-name">GRANITE RIM SUPPLY</span>
  </div>
  <h2 class="service-heading">Specializing in new and used tires &amp; wheels for</h2>
  <p class="service-line">Loaders<span class="dot">•</span>Skid Steers<span class="dot">•</span>Telehandlers<span class="dot">•</span>Boom Lifts<span class="dot">•</span>Forklifts and more</p>
  <h2 class="service-heading">Eliminating downtime</h2>
  <p class="service-line">Wheel Exchange Program for New &amp; Used Foam Filled and Solid Rubber Tires</p>
  <h2 class="service-heading">Specialty services</h2>
  <p class="service-line">Foam Filling Tires<span class="dot">•</span>Largest Tire Press in SE<span class="dot">•</span>ONSITE Forklift Tire Press</p>
  <p class="service-line">Boom Truck Services<span class="dot">•</span>Rubber Tracks</p>
</section>

<section class="card card-front" aria-label="Card front">
  <div class="front-brand">
    <span class="mark-dot"></span>
    <span class="mark-name">GRANITE RIM<br>SUPPLY, LLC</span>
  </div>
  <div class="front-band">
    <div class="person">
      <div class="person-name">Dale Renner</div>
      <div>President</div>
      <div>5126 Marston Lane</div>
      <div>Cedar Point, FL 33499</div>
    </div>
    <div class="divider"></div>
    <ul class="contacts">
      <li><svg viewBox="0 0 16 16" aria-hidden="true"><path d="M1 5c0-2 2-3 7-3s7 1 7 3v1h-4V5H5v1H1zM3 8h10l1 6H2z"/></svg>844-GR-WHEEL</li>
      <li><svg viewBox="0 0 16 16" aria-hidden="true"><path d="M4 0h8a1 1 0 011 1v14a1 1 0 01-1 1H4a1 1 0 01-1-1V1a1 1 0 011-1zm1 2v10h6V2zm3 11a1 1 0 100 2 1 1 0 000-2z"/></svg>836 509 2174</li>
      <li><svg viewBox="0 0 16 16" aria-hidden="true"><path d="M4 0h7v4H4zM1 5h14v8h-3v3H4v-3H1zm4 6v3h6v-3z"/></svg>561-278-9053</li>
      <li><svg viewBox="0 0 16 16" aria-hidden="true"><path d="M0 3h16v1L8 9 0 4zm0 3l8 5 8-5v7H0z"/></svg>dale@graniterim-example.com</li>
    </ul>
  </div>
</section>

</body>
</html>
```